Software Product Flyer Design

A established czech software company needs a marketing flyer to promote their software product and its modules.
The overall feel of the flyer must to be serious, but also eye-catching, enticing, clever and bold to attract customers.
Unifying graphic element is the new product logo.
The flyer would be A4, colour both sides and folded once (to give 4 pages of A5).
Title page - product logo with module name and module icon, short presentation of the product and list of its key features.
Inside pages - detailed informations with screenshots or graphical schemas.
Back side - informations about technical requirements and user support, contacts (address, phone, fax, e-mail, web pages - no social networks).
Product logo, module icon and some images attached.
Updates
Hello,
Reason: For organizational reasons we extending the deadline by 10 days.
FYI: We have uploaded the new ZIP file with previous version of our flyer.
Attached PDF file with text for inner pages.
Target Market(s)
Existing or new customers like municipalities, public authorities and nonprofit organizations.
Industry/Entity Type
Marketing
Requirements
Must have
- Winning designer must provide a template for Adobe InDesign based on his graphic design.
Avoid to using exotic fonts - in Czech we use Latin Extended characters (like áéěíýůčřžšťďň).
Nice to have
- Using graphic motif from product logo like as attached splash screen.

```html
<!DOCTYPE html>
<html lang="en">
<head>
<meta charset="utf-8">
<title>Software Product Flyer</title>
<link rel="stylesheet" href="https://fonts.googleapis.com/css2?family=PT+Sans:wght@400;700&display=swap">
<style>
  :root {
    --backdrop: #e4e2df;
    --paper: #f4f5f6;
    --paper-shade: #e3e5e7;
    --spine: #3d4249;
    --ink: #1d1f22;
    --ink-soft: #3a3d42;
    --accent: #c9501e;
    --band: #e6e7e9;
    --rule: #c2c5c9;
  }
  * { box-sizing: border-box; margin: 0; padding: 0; }
  html, body {
    width: 1200px; height: 900px; overflow: hidden;
    background: var(--backdrop);
    font-family: "PT Sans", Arial, sans-serif;
    color: var(--ink);
  }
  .flyer {
    position: absolute; left: 303px; top: 30px;
    width: 594px; height: 840px;
    background: linear-gradient(160deg, var(--paper) 0%, #ffffff 45%, var(--paper-shade) 100%);
    box-shadow: 0 6px 22px rgba(0,0,0,.18);
    overflow: hidden;
  }
  .flyer__spine {
    position: absolute; left: 0; top: 0; bottom: 0; width: 38px;
    background: var(--spine);
  }
  .flyer__body { position: absolute; left: 38px; right: 0; top: 0; bottom: 0; padding: 28px 30px 0 28px; }
  .intro__title { font-size: 34px; font-weight: 400; line-height: 1.1; margin-bottom: 10px; }
  .intro__text {
    font-size: 11.5px; font-weight: 700; line-height: 1.25; text-align: justify; color: var(--ink);
  }
  .feature { margin-top: 30px; }
  .feature__head {
    display: flex; align-items: center; gap: 14px;
    background: linear-gradient(90deg, transparent 0 30px, var(--band) 30px);
    height: 24px; margin-bottom: 10px;
  }
  .feature__mark { width: 24px; height: 24px; background: var(--accent); flex: none; }
  .feature__name { font-size: 12.5px; font-weight: 700; color: var(--ink-soft); }
  .feature__list { list-style: none; margin-right: 20px; }
  .feature__item {
    position: relative; padding: 5px 0 6px 14px;
    font-size: 9.5px; line-height: 1.45; color: var(--ink-soft);
    border-bottom: 1px solid var(--rule);
  }
  .feature__item::before {
    content: ""; position: absolute; left: 2px; top: 8px;
    border-left: 6px solid var(--ink-soft);
    border-top: 3.5px solid transparent; border-bottom: 3.5px solid transparent;
  }
  .brand {
    position: absolute; right: 34px; bottom: 72px;
    display: flex; align-items: center; gap: 8px;
  }
  .brand__dot { width: 16px; height: 16px; background: var(--accent); }
  .brand__name { font-size: 34px; font-weight: 400; color: var(--accent); line-height: 1; }
  .contact {
    position: absolute; left: 38px; right: 0; bottom: 0; height: 48px;
    display: flex; align-items: center; justify-content: space-between;
    padding: 0 34px 0 20px;
    font-size: 12px; color: var(--ink-soft);
  }
  .contact__item { display: flex; align-items: center; gap: 7px; line-height: 1.15; }
  .contact__icon { width: 20px; height: 20px; flex: none; }
</style>
</head>
<body>
<article class="flyer">
  <div class="flyer__spine"></div>
  <div class="flyer__body">
    <header class="intro">
      <h1 class="intro__title">Lorem Ipsum</h1>
      <p class="intro__text">Lorem ipsum dolor sit amet, consectetur adipisicing elit, sed do eiusmod tempor incididunt ut labore et dolore magna aliqua. Ut enim ad minim veniam, quis nostrud exercitation laboris nisi ut aliquip ex ea commodo consequat. Duis aute irure dolor in reprehenderit in voluptate velit esse cillum dolore eu fugiat nulla pariatur.</p>
    </header>

    <section class="feature" style="margin-top:34px">
      <div class="feature__head"><span class="feature__mark"></span><h2 class="feature__name">Lorem Ipsum</h2></div>
      <ul class="feature__list">
        <li class="feature__item">Lorem ipsum dolor sit amet, consectetur adipisicing elit, sed do eiusmod tempor incididunt ut labore aliqua. Ut enim ad minim veniam, quis Ut enim ad minim veniam, quis</li>
        <li class="feature__item">Ut enim ad minim veniam, quis</li>
        <li class="feature__item">Ut enim ad minim veniam, quis</li>
      </ul>
    </section>

    <section class="feature">
      <div class="feature__head"><span class="feature__mark"></span><h2 class="feature__name">Lorem Ipsum</h2></div>
      <ul class="feature__list">
        <li class="feature__item">Lorem ipsum dolor sit amet, consectetur adipisicing elit, sed do eiusmod tempor incididunt ut labore aliqua. Ut enim ad minim veniam, quis Ut enim ad minim veniam, quis</li>
        <li class="feature__item">Ut enim ad minim veniam, quis</li>
        <li class="feature__item">Ut enim ad minim veniam, quis</li>
      </ul>
    </section>

    <section class="feature">
      <div class="feature__head"><span class="feature__mark"></span><h2 class="feature__name">Lorem Ipsum</h2></div>
      <ul class="feature__list">
        <li class="feature__item">Lorem ipsum dolor sit amet, consectetur adipisicing elit, sed do eiusmod tempor incididunt ut labore aliqua. Ut enim ad minim veniam, quis Ut enim ad minim veniam, quis</li>
        <li class="feature__item">Ut enim ad minim veniam, quis</li>
        <li class="feature__item">Ut enim ad minim veniam, quis</li>
      </ul>
    </section>
  </div>

  <div class="brand">
    <span class="brand__dot"></span>
    <span class="brand__name">velmark</span>
  </div>

  <footer class="contact">
    <div class="contact__item">
      <svg class="contact__icon" viewBox="0 0 20 20" fill="none" stroke="currentColor" stroke-width="1.4" aria-hidden="true">
        <path d="M2 8 L10 2 L18 8"/><rect x="4" y="8" width="12" height="10"/><path d="M8 18 V12 H12 V18"/>
      </svg>
      <span>VELMARK LTD<br>24 Ridge Road, Country</span>
    </div>
    <div class="contact__item">
      <svg class="contact__icon" viewBox="0 0 20 20" fill="none" stroke="currentColor" stroke-width="1.4" aria-hidden="true">
        <circle cx="10" cy="10" r="8"/><rect x="5.5" y="6.5" width="9" height="7"/><path d="M5.5 6.5 L10 10.5 L14.5 6.5"/>
      </svg>
      <span>hello@velmark.com</span>
    </div>
    <div class="contact__item">
      <svg class="contact__icon" viewBox="0 0 20 20" fill="none" stroke="currentColor" stroke-width="1.4" aria-hidden="true">
        <rect x="5" y="2" width="10" height="16" rx="1.5"/><path d="M8 15 H12"/><rect x="7" y="4.5" width="6" height="7"/>
      </svg>
      <span>+1 555 014 220</span>
    </div>
  </footer>
</article>
</body>
</html>
```